Book cover - Lanterns Along the Winding Quay

Book cover for Ebook (Quillet) and wrap around print cover (Bindwell) (back, front, and spine)

The book title (may slightly change by end of brief):
(MAIN TITLE) 'Lanterns Along the Winding Quay'
(SUB HEADING) 'A Practical Seasonal Garden Companion for Planting Bulbs, Pruning Hedges and Growing Fresh Herbs'
by Dr Owen Pratchard

I would like a bold, stand out cover. Contemporary. I would like to avoid stereotypical images of people looking anxious or worried. I would like the design to be more uplifting and hopeful, rather than focusing on the negative aspect of anxiety, but avoiding cliched photos of people raising their hands in the air, smiling and jumping etc. The cover should appeal to both men and women.

Trim size of book cover (for BindWell) is 5.25" x 8" back and front with a spine size of 0.477 inches
Updates

Reason: I have decided to extend the deadline by 1 more day, not because I am unhappy with the quality of the designs, but because a few designers have contacted me to explain they have had technical difficulties when submitting their files. Thanks everyone for the hard work and great designs.

Target Market(s)

Males and females (16+) who struggle with social anxiety and shyness

Industry/Entity Type

Social

Font styles to use
Serif

Requirements
Must have
• Bold cover that is modern and contemporary. For example, I like these covers:
• http://lnkvo.test/7kTq3Wm
• http://lnkvo.test/9gHw5Ze
• http://lnkvo.test/4nVy8Kb
• http://lnkvo.test/6jFu2Xo
• http://lnkvo.test/3mEs9Lt
• http://lnkvo.test/8hGz4Nd
• http://lnkvo.test/5bJk7Pv
Nice to have
• Open to abstract designs.
Should not have
• No stereotypical pictures of people who look anxious or worried. Avoid cliched photos of people raising their hands in the air, smiling and jumping etc.

```html
<!DOCTYPE html>
<html lang="en">
<head>
<meta charset="utf-8">
<title>Lanterns Along the Winding Quay — Book Cover</title>
<link rel="stylesheet" href="https://fonts.googleapis.com/css2?family=Jost:wght@300;400;500;700&display=swap">
<style>
  :root {
    --stage: #d6d6d6;
    --paper-top: #ffffff;
    --paper-bottom: #fbe6d8;
    --ink: #141414;
    --accent-red: #a3131a;
    --disc: #ffffff;
    --art-warm: #f6a04a;
    --art-yellow: #f3dc58;
    --art-green: #a8d46a;
    --art-violet: #c06ad6;
  }
  * { margin: 0; padding: 0; box-sizing: border-box; }
  html, body {
    width: 1200px; height: 900px; overflow: hidden;
    background: var(--stage);
  }
  .canvas { position: relative; width: 1200px; height: 900px; }
  .cover {
    position: absolute; left: 297px; top: 0; width: 635px; height: 900px;
    background: linear-gradient(180deg, var(--paper-top) 0%, var(--paper-top) 40%, var(--paper-bottom) 100%);
    overflow: hidden;
    font-family: "Jost", "Futura", sans-serif;
    color: var(--ink);
  }
  .cover-art {
    position: absolute; left: 10px; top: 60px; width: 615px; height: 820px;
    border-radius: 40px;
    background: linear-gradient(160deg, var(--art-warm) 0%, var(--art-yellow) 40%, var(--art-green) 70%, var(--art-violet) 100%);
    opacity: 0.7;
  }
  .title-disc {
    position: absolute; left: 111px; top: 165px; width: 410px; height: 410px;
    border-radius: 50%; background: var(--disc);
    display: flex; flex-direction: column; align-items: center; justify-content: center;
    text-align: center; font-weight: 300;
  }
  .title-kicker {
    font-weight: 700; font-size: 29px; letter-spacing: 7px;
    color: var(--accent-red); line-height: 1; margin-bottom: 6px;
  }
  .title-line {
    font-weight: 300; font-size: 64px; line-height: 1; letter-spacing: 0.5px;
  }
  .title-joiner { font-weight: 400; font-size: 30px; line-height: 1.05; }
  .subtitle {
    position: absolute; left: 82px; top: 588px; width: 471px;
    text-align: center; font-weight: 400; font-size: 24px; line-height: 1.2;
  }
  .author {
    position: absolute; left: 0; top: 800px; width: 635px;
    text-align: center; font-weight: 500; font-size: 25px; letter-spacing: 12px;
  }
</style>
</head>
<body>
  <main class="canvas">
    <section class="cover">
      <div class="cover-art" role="img" aria-label="Abstract rainbow watercolour splash artwork in red, orange, yellow, green, violet and magenta"></div>
      <h1 class="title-disc">
        <span class="title-kicker">LANTERNS</span>
        <span class="title-line">ALONG</span>
        <span class="title-joiner">the</span>
        <span class="title-line">WINDING</span>
        <span class="title-line">QUAY</span>
      </h1>
      <p class="subtitle">A Practical Seasonal Garden Companion for Planting Bulbs, Pruning Hedges and Growing Fresh Herbs</p>
      <p class="author">DR OWEN PRATCHARD</p>
    </section>
  </main>
</body>
</html>
```